brightquokka.net we need a webpage designed for our new product

We need a webpage designed for our new range of products from our new brand. We have had a logo designed on sketchharbor (see attached) and we want to keep to this theme. Our first product is a range of affordable app controlled LED lightbulbs.

I have added some photos that we think is good inspirational material and would be good as a background to this website, but we want the site to look modern but not conventional. We would like something that makes our company look quirky not corporate.

Thats it

Target Market(s)

Our product is being stocked by big name online retailers in the UK, the page will get link through hits from our app. Our target market is gadget freaks of all ages.

Industry/Entity Type

It Company

Requirements
Must have
• We are going to need a help page, text to be uploaded next few days.

We need a contact page.

design my work on iOS and Android as most people will access page through their handset or tablet.
Should not have
• We do not want anything too corporate.

```html
<!DOCTYPE html>
<html lang="en">
<head>
<meta charset="utf-8">
<title>BrightQuokka</title>
<link href="https://fonts.googleapis.com/css2?family=Open+Sans:wght@400;600;700&display=swap" rel="stylesheet">
<style>
:root{
  --green:#3dbb4a;
  --green-dark:#2a7d2a;
  --text:#333;
  --nav:#2f2f2f;
  --band:#ececec;
  --label:#f5f5f5;
  --client:#8a8a8a;
  --footer-top:#575757;
  --footer-bottom:#262626;
  --white:#fff;
}
*{margin:0;padding:0;box-sizing:border-box}
html,body{width:830px;height:1200px;overflow:hidden;background:var(--white)}
body{position:relative;font-family:"Open Sans",Arial,sans-serif;color:var(--text)}
.abs{position:absolute}
.brand{left:67px;top:8px;width:99px;height:110px;display:flex;flex-direction:column;align-items:center;justify-content:flex-end;gap:6px}
.brand-mark{width:46px;height:46px;border-radius:50%;background:var(--green)}
.brand-name{font-size:7px;font-weight:700;color:var(--green-dark);letter-spacing:.3px}
.contact-bar{left:512px;top:40px;display:flex;align-items:center;gap:6px;font-size:10px}
.social-top{left:685px;top:37px;display:flex;gap:2px}
.social-top span{width:24px;height:24px;border-radius:3px;display:block}
.nav{left:166px;top:80px;width:595px;height:42px;background:var(--nav);display:flex}
.nav a{color:var(--white);text-decoration:none;font-size:12px;display:flex;align-items:center;justify-content:center;height:100%;border-right:1px solid #444}
.nav a.active{background:var(--green)}
.hero{left:67px;top:122px;width:694px;height:379px;
  background:radial-gradient(ellipse at 22% 62%,#f3ede6 0,#e1d4c6 18%,rgba(120,80,50,0) 40%),linear-gradient(120deg,#5a3b24,#8c5d3a 40%,#6d4730 70%,#3f2a1c)}
.hero-text{left:250px;top:273px;width:490px;text-align:center;color:var(--white);font-size:16px;line-height:28px;font-family:Arial,sans-serif;text-shadow:0 1px 2px rgba(0,0,0,.3)}
.slider-ctrl{left:338px;top:477px;width:124px;height:19px;background:#eee;border:1px solid #ccc;border-radius:3px;display:flex;align-items:center}
.slider-ctrl .arrows{width:36px;height:100%;border-right:1px solid #ccc;display:flex;align-items:center;justify-content:center}
.dots{display:flex;gap:5px;padding-left:10px}
.dots i{width:7px;height:7px;border-radius:50%;background:#aaa;display:block}
.dots i.on{background:#222}
.welcome-photo{left:68px;top:532px;width:226px;height:146px;background:linear-gradient(135deg,#e84b2a,#f2b32c 40%,#c8821e 70%,#6b3b1c)}
.welcome h2{left:318px;top:527px;font-size:16px;font-weight:400;color:#222}
.welcome p{left:318px;top:557px;width:436px;font-size:10px;line-height:15.3px;text-align:justify}
.btn{left:319px;top:647px;width:79px;height:27px;background:linear-gradient(#3a9a3a,#1f6e1f);border-radius:3px;color:var(--white);font-size:9.5px;display:flex;align-items:center;justify-content:center;border:1px solid #1a5e1a}
.divider{left:68px;top:709px;width:691px;height:1px;background:#aaa}
.section-title{left:71px;top:721px;font-size:16px;word-spacing:3px;color:#222}
.carousel-nav{left:724px;top:721px;display:flex;gap:2px}
.carousel-nav span{width:17px;height:17px;background:#777;display:flex;align-items:center;justify-content:center}
.product{top:758px;width:226px}
.product .photo{height:124px}
.product h3{font-size:16px;font-weight:400;color:var(--green-dark);text-align:center;margin-top:4px}
.product p{font-size:10px;line-height:15.4px;text-align:justify;padding:0 8px;margin-top:2px}
.clients{left:66px;top:992px;width:694px;height:54px;background:var(--band);display:flex;align-items:center}
.clients .label{width:116px;height:100%;background:var(--label);font-size:12px;line-height:13px;padding:14px 0 0 13px;letter-spacing:-.3px}
.clients .name{font-weight:700;color:var(--client);font-size:24px;margin-left:22px}
.footer{left:0;top:1072px;width:830px;height:128px;background:linear-gradient(var(--footer-top),var(--footer-bottom));color:var(--white)}
.footer-links{left:0;top:25px;width:830px;text-align:center;font-size:9px;font-family:Arial,sans-serif}
.copyright{left:69px;top:78px;font-size:8px;font-family:Arial,sans-serif}
.social-foot{left:316px;top:65px;display:flex;gap:5px}
.social-foot span{width:28px;height:28px;border-radius:50%;background:#eee;display:block;border:2px solid #999}
.newsletter{left:588px;top:70px;width:167px;height:20px;background:var(--white);display:flex;align-items:center;justify-content:space-between;padding:0 4px 0 6px;color:#666;font-size:8px}
.version{left:800px;top:104px;font-size:8px}
</style>
</head>
<body>
<div class="abs brand"><span class="brand-mark"></span><span class="brand-name">BRIGHTQUOKKA</span></div>

<div class="abs contact-bar">
  <svg width="12" height="16" viewBox="0 0 12 16"><rect x="1" y="0.5" width="10" height="15" rx="2" fill="none" stroke="#3dbb4a" stroke-width="1.6"/><circle cx="6" cy="13" r="1" fill="#3dbb4a"/></svg>
  <span>555-014-2210 ,&nbsp; 555-019-3377</span>
</div>
<div class="abs social-top" aria-label="Social links">
  <span style="background:#5bb6e6"></span><span style="background:#3b5b98"></span><span style="background:#333"></span>
</div>

<nav class="abs nav">
  <a class="active" style="width:70px">HOME</a>
  <a style="width:88px">ABOUT US</a>
  <a style="width:84px">SERVICE</a>
  <a style="width:111px">TESTIMONAL</a>
  <a style="width:66px;border:0">NEWS</a>
  <a style="width:66px;border:0">BLOG</a>
  <a style="width:110px;border:0">CONTACT US</a>
</nav>

<div class="abs hero" role="img" aria-label="Photo of a white ceramic seal lamp in a vintage shop"></div>
<div class="abs hero-text">OUR FIRST PRODUCT IS A RANGE OF AFFORDABLE<br>APP CONTROLLED LED LIGHTBULBS</div>
<div class="abs slider-ctrl">
  <div class="arrows"><svg width="20" height="9" viewBox="0 0 20 9"><path d="M6 1L2 4.5 6 8" fill="none" stroke="#111" stroke-width="1.6"/><path d="M14 1l4 3.5-4 3.5" fill="none" stroke="#888" stroke-width="1.2"/></svg></div>
  <div class="dots"><i></i><i></i><i class="on"></i><i></i><i></i><i></i></div>
</div>

<section class="welcome">
  <div class="abs welcome-photo" role="img" aria-label="Photo of cartoon cat telephones on a shelf"></div>
  <h2 class="abs">WELCOME TO BRIGHTQUOKKA</h2>
  <p class="abs">Lorem ipsum dolor sit amet, consectetur adipiscing elit. Donec nec justo sem. Morbi suscipit augue id risus egestas a imperdiet augue mattis. Suspendisse potenti. Donec varius, turpis sit amet interdum tristique, turpis tortor varius sem, ac porta ipsum est non tortor. Cras tristique, sapien in accumsan tempor Lorem ipsum dolor sit amet, consectetur adipiscing elit. Donec nec justo sem. Morbi suscipit augue id risus egestas a imperdiet augue mattis. Suspendisse potenti.</p>
  <div class="abs btn">READ MORE</div>
</section>

<div class="abs divider"></div>
<h2 class="abs section-title" style="font-weight:400">OUR PRODUCT</h2>
<div class="abs carousel-nav">
  <span><svg width="7" height="10"><path d="M5 1L2 5l3 4" fill="none" stroke="#fff" stroke-width="1.3"/></svg></span>
  <span><svg width="7" height="10"><path d="M2 1l3 4-3 4" fill="none" stroke="#fff" stroke-width="1.3"/></svg></span>
</div>

<div class="abs product" style="left:70px">
  <div class="photo" role="img" aria-label="Photo of vintage toy cars and a figure statue" style="background:linear-gradient(120deg,#6b4a3a,#b03a34 45%,#8c6a52 70%,#3a4a7a)"></div>
  <h3>Product Name</h3>
  <p>Lorem ipsum dolor sit amet, consectetur adipiscing elit. Donec nec justo sem. Morbi suscipit augue id risus egestas a</p>
</div>
<div class="abs product" style="left:302px">
  <div class="photo" role="img" aria-label="Photo of hanging vintage lamps in a shop" style="background:radial-gradient(circle at 50% 55%,#f4d08a,#a06a32 45%,#3d2616)"></div>
  <h3>Product Name</h3>
  <p>Lorem ipsum dolor sit amet, consectetur adipiscing elit. Donec nec justo sem. Morbi suscipit augue id risus egestas a</p>
</div>
<div class="abs product" style="left:535px">
  <div class="photo" role="img" aria-label="Photo of a crowded antique store interior" style="background:linear-gradient(180deg,#4a3a2c,#8a7462 45%,#6a5a60 70%,#9a4a3a)"></div>
  <h3>Product Name</h3>
  <p>Lorem ipsum dolor sit amet, consectetur adipiscing elit. Donec nec justo sem. Morbi suscipit augue id risus egestas a</p>
</div>

<div class="abs clients">
  <div class="label">OUR MOST<br>RECENT CLIENTS</div>
  <span class="name" style="margin-left:20px">BRISKLY</span>
  <span class="name" style="font-size:30px">QV58</span>
  <span class="name" style="font-size:18px">NORTHPINE</span>
  <span class="name" style="font-size:20px">LATTICE</span>
  <span class="name" style="font-size:20px">EVERMORE</span>
</div>

<footer class="abs footer">
  <div class="abs footer-links">Terms of Service | Returns | Policy Privacy | Event | Contact | Blog | Sitemap</div>
  <div class="abs copyright">Copy Right © 2014. All rights reserved.</div>
  <div class="abs social-foot" aria-label="Social links"><span></span><span></span><span></span><span></span><span></span><span></span></div>
  <div class="abs newsletter"><span>News Letter</span>
    <svg width="24" height="15" viewBox="0 0 24 15"><rect x="1" y="1" width="22" height="13" fill="none" stroke="#222" stroke-width="1.6"/><path d="M1 1l11 8 11-8" fill="none" stroke="#222" stroke-width="1.6"/></svg>
  </div>
  <div class="abs version">C6</div>
</footer>
</body>
</html>
```